TA BRAMLEY BUSINESS CARD DESIGN PROJECT

We need to utilize our logo that was expertly created on PixelHarbor and now need to match this with a business card design.

```html
<!DOCTYPE html>
<html lang="en">
<head>
<meta charset="utf-8">
<title>TA BRAMLEY Business Card</title>
<link rel="stylesheet" href="https://fonts.googleapis.com/css2?family=Montserrat:wght@400;500;700;800&display=swap">
<style>
  :root {
    --backdrop: #474747;
    --card-black: #181818;
    --brand-blue: #0f58ad;
    --brand-blue-deep: #0c4f9c;
    --ink-white: #ffffff;
  }
  * { box-sizing: border-box; margin: 0; padding: 0; }
  html, body {
    width: 1200px;
    height: 801px;
    overflow: hidden;
    background: var(--backdrop);
    font-family: "Montserrat", sans-serif;
  }
  .canvas {
    position: relative;
    width: 1200px;
    height: 801px;
    display: flex;
    align-items: center;
    justify-content: center;
    gap: 60px;
  }
  .card {
    position: relative;
    width: 520px;
    height: 298px;
    border-radius: 14px;
    overflow: hidden;
  }
  /* Front */
  .card-front { background: var(--card-black); }
  .front-band {
    position: absolute;
    left: 0; bottom: 0;
    width: 100%;
    height: 22px;
  }
  .brand-lockup {
    position: absolute;
    left: 30px;
    top: 128px;
    display: flex;
    align-items: center;
    gap: 10px;
  }
  .brand-mark {
    width: 16px;
    height: 16px;
    background: var(--brand-blue);
  }
  .brand-name {
    color: var(--brand-blue);
    font-weight: 800;
    font-size: 26px;
    letter-spacing: 1px;
  }
  .divider {
    position: absolute;
    left: 240px;
    top: 56px;
    width: 1px;
    height: 178px;
    background: var(--brand-blue);
  }
  .contact {
    position: absolute;
    left: 262px;
    top: 50px;
    color: var(--ink-white);
  }
  .contact-name {
    color: var(--brand-blue);
    font-weight: 800;
    font-size: 21px;
    letter-spacing: 0.5px;
    line-height: 1.1;
  }
  .contact-title {
    font-size: 13px;
    font-weight: 400;
    margin-top: 4px;
  }
  .contact-list {
    list-style: none;
    margin-top: 16px;
    font-size: 12.5px;
    line-height: 1.55;
  }
  .contact-list li { display: flex; align-items: center; gap: 8px; }
  .contact-icon { width: 11px; height: 11px; flex: none; }
  .contact-address {
    margin-top: 14px;
    font-size: 12.5px;
    line-height: 1.5;
    font-style: normal;
  }
  /* Back */
  .card-back {
    background: var(--brand-blue);
    display: flex;
    align-items: center;
    justify-content: center;
  }
  .back-brand {
    color: var(--brand-blue-deep);
    font-weight: 800;
    font-size: 58px;
    letter-spacing: 4px;
  }
</style>
</head>
<body>
<main class="canvas">
  <section class="card card-front" aria-label="Card front">
    <svg class="front-band" viewBox="0 0 520 22" preserveAspectRatio="none" aria-hidden="true">
      <polygon points="0,14 300,14 320,4 520,4 520,22 0,22" fill="var(--brand-blue)"/>
    </svg>
    <div class="brand-lockup">
      <span class="brand-mark"></span>
      <span class="brand-name">TA BRAMLEY</span>
    </div>
    <div class="divider"></div>
    <div class="contact">
      <h1 class="contact-name">MARCUS HALE</h1>
      <p class="contact-title">Managing Director</p>
      <ul class="contact-list">
        <li>
          <svg class="contact-icon" viewBox="0 0 12 12"><path d="M2 1h3l1 3-2 1a7 7 0 0 0 3 3l1-2 3 1v3c-6 0-9-3-9-9z" fill="var(--brand-blue)"/></svg>
          123 456 789
        </li>
        <li>
          <svg class="contact-icon" viewBox="0 0 12 12"><rect x="1" y="3" width="10" height="8" rx="1" fill="var(--brand-blue)"/><rect x="3" y="1" width="6" height="3" fill="var(--brand-blue)"/></svg>
          123 456 789
        </li>
        <li>
          <svg class="contact-icon" viewBox="0 0 12 12"><rect x="1" y="2.5" width="10" height="7" fill="var(--brand-blue)"/><path d="M1 2.5l5 4 5-4" stroke="var(--card-black)" fill="none"/></svg>
          info@yourmail.com
        </li>
        <li>
          <svg class="contact-icon" viewBox="0 0 12 12"><circle cx="6" cy="6" r="5" fill="var(--brand-blue)"/><path d="M1 6h10M6 1c-2 2.5-2 7.5 0 10M6 1c2 2.5 2 7.5 0 10" stroke="var(--card-black)" stroke-width="0.8" fill="none"/></svg>
          www.yourwebsite.com
        </li>
      </ul>
      <address class="contact-address">Your address, City<br>State, Zip 1234</address>
    </div>
  </section>

  <section class="card card-back" aria-label="Card back">
    <span class="back-brand">TA BRAMLEY</span>
  </section>
</main>
</body>
</html>
```